Local Roofing/Construction company business needs new biz card design

We need a new business card design, current cards are from the start of this operation and generic at best. We are a local Construction Company (General Contractor) with a majority of our work originating from insurance claims-exterior finish work is the main focus (Roofs-Siding-Gutters etc). Heavily involved with homeowners and the low ball offers they receive from insurance company's after a insurable event takes place. I have attached some of our original logo file(s) below.

```html
<!DOCTYPE html>
<html lang="en">
<head>
<meta charset="utf-8">
<title>Bolt Ridge Construction – Business Card</title>
<link href="https://fonts.googleapis.com/css2?family=Montserrat:wght@400;500;700;800&display=swap" rel="stylesheet">
<style>
  :root {
    --green: #2fd474;
    --green-edge: #27c267;
    --ink: #2b2b2b;
    --card-black: #151515;
    --card-white: #ffffff;
    --stage: #e9ebea;
  }
  * { margin: 0; padding: 0; box-sizing: border-box; }
  html, body {
    width: 1200px;
    height: 900px;
    overflow: hidden;
    background: var(--stage);
    font-family: "Montserrat", sans-serif;
  }
  .sheet {
    width: 1200px;
    height: 900px;
    display: flex;
    align-items: center;
    justify-content: center;
    gap: 30px;
  }
  .card {
    position: relative;
    width: 560px;
    height: 320px;
    border-radius: 22px;
    overflow: hidden;
    border-bottom: 5px solid var(--green-edge);
  }
  /* Back face */
  .card--back { background: var(--card-black); }
  .back-pattern {
    position: absolute;
    inset: 0;
    background: linear-gradient(115deg, #5a5a5a 0%, #2c2c2c 40%, #111 70%, #1a1a1a 100%);
  }
  .back-name {
    position: absolute;
    right: 40px;
    top: 40px;
    display: flex;
    align-items: center;
    gap: 10px;
    color: var(--green);
    font-weight: 800;
    font-size: 20px;
    letter-spacing: 0.5px;
  }
  .back-name .mark-square { width: 16px; height: 16px; background: var(--green); }
  /* Front face */
  .card--front {
    background: var(--card-white);
    display: flex;
    align-items: center;
  }
  .brand {
    width: 260px;
    display: flex;
    flex-direction: column;
    align-items: center;
    gap: 14px;
    padding-left: 20px;
  }
  .brand .mark-square {
    width: 96px;
    height: 96px;
    background: var(--green);
    border-radius: 12px;
  }
  .brand-name {
    color: var(--green);
    font-weight: 800;
    font-size: 19px;
    text-align: center;
    line-height: 1.2;
    letter-spacing: 0.5px;
  }
  .divider {
    width: 2px;
    height: 150px;
    background: var(--green);
    margin: 0 26px 0 4px;
  }
  .contact { color: var(--ink); }
  .contact-name {
    color: var(--green);
    font-weight: 700;
    font-size: 24px;
    line-height: 1.1;
  }
  .contact-role {
    font-size: 13px;
    font-weight: 500;
    margin: 4px 0 16px;
  }
  .contact-list { list-style: none; font-size: 12.5px; line-height: 1.45; }
  .contact-list li { display: flex; align-items: flex-start; gap: 8px; }
  .contact-list svg { width: 11px; height: 11px; flex: none; margin-top: 3px; fill: var(--green); }
  .contact-list .no-icon { padding-left: 19px; }
</style>
</head>
<body>
<main class="sheet">
  <section class="card card--back">
    <div class="back-pattern" role="img" aria-label="Repeating tonal pattern of the company monogram in gloss black on matte black"></div>
    <div class="back-name"><span class="mark-square"></span>Bolt Ridge</div>
  </section>

  <section class="card card--front">
    <div class="brand">
      <span class="mark-square"></span>
      <p class="brand-name">BOLT RIDGE<br>CONSTRUCTION</p>
    </div>
    <div class="divider"></div>
    <div class="contact">
      <h1 class="contact-name">Dana Whitfield</h1>
      <p class="contact-role">Owner</p>
      <ul class="contact-list">
        <li><svg viewBox="0 0 24 24"><path d="M6.6 10.8a15.1 15.1 0 0 0 6.6 6.6l2.2-2.2a1 1 0 0 1 1-.25 11.4 11.4 0 0 0 3.6.57 1 1 0 0 1 1 1V20a1 1 0 0 1-1 1A17 17 0 0 1 3 4a1 1 0 0 1 1-1h3.5a1 1 0 0 1 1 1c0 1.25.2 2.45.57 3.57a1 1 0 0 1-.25 1z"/></svg>555-210-4477</li>
        <li><svg viewBox="0 0 24 24"><path d="M2 5h20v14H2zm2 2v.4l8 5 8-5V7z"/></svg>info@boltridgebuild.com</li>
        <li><svg viewBox="0 0 24 24"><circle cx="12" cy="12" r="10"/></svg>www.boltridgebuild.com</li>
        <li><svg viewBox="0 0 24 24"><path d="M12 2a7 7 0 0 0-7 7c0 5 7 13 7 13s7-8 7-13a7 7 0 0 0-7-7zm0 9.5A2.5 2.5 0 1 1 12 6.5a2.5 2.5 0 0 1 0 5z"/></svg>48 Alder Creek Ln</li>
        <li class="no-icon">Millbrook, MO 60000</li>
      </ul>
    </div>
  </section>
</main>
</body>
</html>
```